Stonebrace Business Card Design

The Stonebrace Co is an aggregate (crushing) equipment dealer serving Western Canadian provinces. Stonebrace is a distributor of aggregate equipment for different manufacturers.

We are looking to change and update the existing business card which has been used since the existence of the company. A copy of existing card has been attached for reference. The Stonebrace Co logo we want to remain the same and we want the green color to remain the same.

We are wanting something new with a different look. A refreshing card to show a new modern and updated look. No longer wanting to have the manufacturers on the back of the card but something more like our logo on the back of the card with a statement like "Crushing Solutions"

ideas could be:
- card can be different colors on front and back
- front or reverse of the card could possibly be the green color with the logo in black

Target Market(s)

Owners of Aggregate/Crushing companies

Contact Information for Business Card

see above

Requirements
Must have
• - logo to remain same along with same font within logo
• - green color to remain same
Nice to have
• as noted above under project description
Should not have

```html
<!DOCTYPE html>
<html lang="en">
<head>
<meta charset="utf-8">
<title>Stonebrace Co Business Card</title>
<link rel="stylesheet" href="https://fonts.googleapis.com/css2?family=Montserrat:wght@400;500;800&family=Open+Sans:wght@400;600&display=swap">
<style>
  :root {
    --olive: #8f8d36;
    --ink: #1f1d1e;
    --paper: #ffffff;
    --backdrop: #d9d9d7;
    --text: #222222;
  }
  * { box-sizing: border-box; margin: 0; padding: 0; }
  html, body { width: 1200px; height: 1000px; overflow: hidden; }
  body { background: var(--backdrop); position: relative; font-family: "Open Sans", Arial, sans-serif; color: var(--text); }

  .card {
    position: absolute;
    width: 600px;
    height: 343px;
    background: var(--paper);
    overflow: hidden;
    box-shadow: 0 6px 18px rgba(0,0,0,0.18);
  }

  /* Reverse side */
  .card--reverse { left: 110px; top: 80px; }
  .reverse__field {
    position: absolute; left: 0; top: 0; width: 100%; height: 236px;
    background: var(--olive);
  }
  .reverse__brand {
    position: absolute; left: 0; right: 0; top: 96px;
    display: flex; align-items: center; justify-content: center; gap: 14px;
  }
  .brand-dot { width: 34px; height: 34px; border-radius: 50%; background: var(--ink); }
  .reverse__name {
    font-family: "Montserrat", Arial, sans-serif; font-weight: 800;
    font-size: 30px; letter-spacing: 0.5px; color: var(--ink);
  }
  .reverse__lines {
    position: absolute; left: 0; right: 0; top: 274px;
    text-align: center;
    font-family: "Montserrat", Arial, sans-serif; font-weight: 400;
    font-size: 19px; letter-spacing: 1px; color: var(--text);
  }
  .reverse__lines .sep { display: inline-block; width: 1.5px; height: 22px; background: var(--text); margin: 0 12px; vertical-align: -4px; }

  /* Front side */
  .card--front { left: 490px; top: 500px; }
  .front__shapes { position: absolute; inset: 0; }
  .front__brand {
    position: absolute; right: 28px; top: 40px;
    font-family: "Montserrat", Arial, sans-serif; font-weight: 800;
    font-size: 17px; color: var(--paper); letter-spacing: 0.3px;
  }
  .front__person {
    position: absolute; left: 34px; top: 104px;
    font-family: "Montserrat", Arial, sans-serif; font-weight: 500;
    font-size: 27px; color: var(--paper); letter-spacing: 0.5px;
  }
  .front__address {
    position: absolute; right: 20px; top: 121px;
    font-size: 12.5px; font-weight: 600; color: var(--paper); letter-spacing: 0.4px;
    text-transform: uppercase;
  }
  .contact-list { position: absolute; list-style: none; }
  .contact-list li { display: flex; align-items: center; gap: 14px; font-size: 23px; line-height: 32px; }
  .contact-list svg { width: 18px; height: 18px; fill: var(--ink); flex: none; }
  .contact-list--phones { left: 36px; top: 198px; }
  .contact-list--online { left: 330px; top: 166px; }
  .contact-list--online li { font-size: 21px; line-height: 30px; }
</style>
</head>
<body>

  <section class="card card--reverse" aria-label="Business card reverse">
    <div class="reverse__field"></div>
    <div class="reverse__brand">
      <span class="brand-dot"></span>
      <span class="reverse__name">THE STONEBRACE CO.</span>
    </div>
    <p class="reverse__lines">SCREENERS<span class="sep"></span>CRUSHERS<span class="sep"></span>STACKERS</p>
  </section>

  <section class="card card--front" aria-label="Business card front">
    <svg class="front__shapes" viewBox="0 0 600 343" width="600" height="343" aria-hidden="true">
      <rect x="0" y="0" width="600" height="152" fill="var(--olive)"/>
      <path d="M330 112 H600 V150 H352 Q340 150 336 138 Z" fill="var(--ink)"/>
      <rect x="0" y="152" width="600" height="191" fill="var(--paper)"/>
    </svg>

    <div class="front__brand">THE STONEBRACE CO.</div>
    <h1 class="front__person">DALE MORROW</h1>
    <p class="front__address">2210-48B Avenue, Nisku, Alberta T9E 1K2</p>

    <ul class="contact-list contact-list--phones">
      <li>
        <svg viewBox="0 0 24 24" aria-label="Office"><path d="M3 7c0-2 3-3 9-3s9 1 9 3v2h-5V7.5c-1-.4-2.5-.5-4-.5s-3 .1-4 .5V9H3zM6 11h12l2 8H4zm6 2a2.5 2.5 0 1 0 0 5 2.5 2.5 0 0 0 0-5z"/></svg>
        <span>780 . 555 . 0142</span>
      </li>
      <li>
        <svg viewBox="0 0 24 24" aria-label="Mobile"><path d="M6.6 10.8a15 15 0 0 0 6.6 6.6l2.2-2.2a1 1 0 0 1 1-.25 11.4 11.4 0 0 0 3.6.57 1 1 0 0 1 1 1V20a1 1 0 0 1-1 1A17 17 0 0 1 3 4a1 1 0 0 1 1-1h3.5a1 1 0 0 1 1 1c0 1.25.2 2.45.57 3.6a1 1 0 0 1-.25 1z"/></svg>
        <span>780 . 555 . 0187</span>
      </li>
      <li>
        <svg viewBox="0 0 24 24" aria-label="Fax"><path d="M7 3h10v5H7zM4 9h16a1 1 0 0 1 1 1v7h-4v4H7v-4H3v-7a1 1 0 0 1 1-1zm5 7v3h6v-3z"/></svg>
        <span>780 . 555 . 0163</span>
      </li>
    </ul>

    <ul class="contact-list contact-list--online">
      <li>
        <svg viewBox="0 0 24 24" aria-label="Email"><path d="M2 5h20v14H2zm2 2v.5l8 5.5 8-5.5V7zm0 3v7h16v-7l-8 5.5z"/></svg>
        <span>dale@stonebrace.com</span>
      </li>
      <li>
        <svg viewBox="0 0 24 24" aria-label="Website"><path d="M12 2a10 10 0 1 0 0 20 10 10 0 0 0 0-20zm6.9 6h-3a15 15 0 0 0-1.3-3.9A8 8 0 0 1 18.9 8zM12 4c.9 1.2 1.6 2.6 2 4h-4c.4-1.4 1.1-2.8 2-4zM4.3 14a8 8 0 0 1 0-4h3.3a16 16 0 0 0 0 4zm.8 2h3a15 15 0 0 0 1.3 3.9A8 8 0 0 1 5.1 16zm3-8h-3a8 8 0 0 1 4.3-3.9A15 15 0 0 0 8.1 8zM12 20c-.9-1.2-1.6-2.6-2-4h4c-.4 1.4-1.1 2.8-2 4zm2.3-6H9.7a14 14 0 0 1 0-4h4.6a14 14 0 0 1 0 4zm.3 5.9a15 15 0 0 0 1.3-3.9h3a8 8 0 0 1-4.3 3.9zM16.4 14a16 16 0 0 0 0-4h3.3a8 8 0 0 1 0 4z"/></svg>
        <span>www.stonebrace.ca</span>
      </li>
    </ul>
  </section>

</body>
</html>
```